BRTL web site redesign

Coastal Linkage Engineering service (BRTL) is a diverse technology company specialising in design and installation of fibre optics, network convergence and building services, for commercial clients in Australia, we required a new design of our website to attract new clients, generate sales leads, and provide information about our services to the market. The site and should have a new technology look and feel and be designed in word press. our branding colour is blue.

Target Market(s)

New developments, Construction organisations, Commercial end users, IT managers, Consultants.

Industry/Entity Type

It Company

Number of Pages Required

5+ page

Font styles to use
Sans Serif

Colors
0292cd
3176b5

Requirements
Must have
• key pages.
• Home page with some sizzle, automated pictures running through, I like the look of this competitor website http://www.gleamwirex.com.au/ good clean menus and easy to navigate.
• Services page our key services are Fibre optics, Security, Building services,Electrical. I would like the same page layout (Design) for all our services, with a find out more link on each page, manly picture driven with text around our key messaging.
• About us page with space for company profile and directors pictures, bio and contact information.
• Certifications / Accreditations page with have over 20 certifications on different products from suppliers, and a number of licences from governing bodies.
• Current and past projects page with case studies and customer outcomes
• Contact us page with options around what services they require more information on, please keep in mind the site is around generating sales Leeds and being seen as an industry expert.
Nice to have
• RSS feeds, Linked in link, to be placed within the design, Consistent BRTL branding,Same colour blue as our logo Document library for education information, white papers, presentations etc,
• a new technology look and feel, mobile friendly.
Should not have
• boring layout, move away from our cuurent website http://www.brtlgroup.com.au/
• no e eCommerce store required.

```html
<!DOCTYPE html>
<html lang="en">
<head>
<meta charset="utf-8">
<title>BRTL – Coastal Linkage Engineering Service</title>
<link href="https://fonts.googleapis.com/css2?family=Open+Sans:wght@400;600;700&family=Raleway:wght@400;500;600&display=swap" rel="stylesheet">
<style>
:root{
  --brand:#0292cd;
  --brand-deep:#3176b5;
  --nav-top:#1aa3dc;
  --nav-bottom:#0184bd;
  --ink:#222;
  --body:#333;
  --muted:#7a7a7a;
  --black:#000;
  --white:#fff;
  --caption:rgba(18,38,70,.88);
}
*{box-sizing:border-box;margin:0;padding:0}
html,body{width:1200px;height:2256px;overflow:hidden;background:var(--white)}
body{position:relative;font-family:"Open Sans",Arial,sans-serif;color:var(--body)}
.abs{position:absolute}

/* header */
.site-header{position:absolute;left:0;top:0;width:1200px;height:131px}
.brand{position:absolute;left:57px;top:34px;display:flex;align-items:center;gap:14px}
.brand-mark{width:22px;height:22px;background:var(--brand)}
.brand-name{font-family:"Open Sans",sans-serif;font-weight:700;font-size:54px;line-height:1;color:var(--brand);letter-spacing:1px}
.brand-sub{position:absolute;left:57px;top:100px;font-size:10px;font-weight:700;color:var(--brand);text-transform:uppercase;letter-spacing:.2px}
.support{position:absolute;right:56px;top:64px;text-align:right;font-family:"Raleway",sans-serif}
.support-label{font-size:16px;color:#777}
.support-number{font-size:25px;color:var(--ink);font-weight:500;display:flex;align-items:center;gap:6px;margin-top:2px}

/* nav */
.main-nav{position:absolute;left:0;top:131px;width:1200px;height:48px;background:linear-gradient(var(--nav-top),var(--nav-bottom))}
.nav-item{position:absolute;top:0;height:48px;line-height:48px;font-family:"Raleway",sans-serif;font-weight:600;font-size:16px;color:var(--white);text-transform:uppercase}
.nav-item.active{background:var(--brand-deep);padding:0 30px}
.submenu{position:absolute;left:173px;top:179px;width:194px;height:117px;background:var(--brand-deep);z-index:3;padding:12px 0 0 31px}
.submenu li{list-style:none;font-family:"Raleway",sans-serif;font-weight:600;font-size:11px;color:var(--white);text-transform:uppercase;height:23.5px}

/* hero */
.hero{position:absolute;left:0;top:179px;width:1200px;height:543px;background:
  radial-gradient(circle at 75% 40%,#3a3f46 0%,#24272c 35%,transparent 60%),
  radial-gradient(circle at 90% 15%,#3b86c6 0%,transparent 30%),
  linear-gradient(110deg,#3b4a52 0%,#6d7d76 25%,#8c8577 50%,#2f3236 75%,#a79c8d 100%)}
.hero-caption{position:absolute;left:53px;top:343px;width:439px;height:207px;background:var(--caption);color:var(--white);font-family:"Raleway",sans-serif;padding:28px 37px}
.hero-kicker{font-size:27px;font-weight:400;line-height:1.2}
.hero-title{font-size:34px;font-weight:500;line-height:1.25;margin-top:4px}
.hero-text{font-family:"Open Sans",sans-serif;font-size:13px;line-height:23px;margin-top:6px;color:#dfe6ee}
.hero-dots{display:flex;gap:5px;margin-top:10px}
.hero-dots span{width:14px;height:14px;border-radius:50%;border:2px solid var(--white);background:var(--brand-deep)}
.hero-dots span:first-child{background:var(--white)}

/* about */
.section-title{position:absolute;font-size:25px;font-weight:400;color:var(--ink);text-shadow:0 1px 2px rgba(0,0,0,.25)}
.about-text{position:absolute;left:53px;top:822px;width:1095px;font-size:12.5px;line-height:24px;color:var(--body)}

/* services */
.service{position:absolute;top:920px;width:243px}
.service-photo{width:243px;height:157px;border:2px solid #111;box-shadow:0 2px 4px rgba(0,0,0,.4)}
.service-title{font-size:19px;font-weight:600;color:var(--brand);margin-top:14px}
.service-text{font-size:12.5px;line-height:22.5px;color:var(--body);margin-top:3px}
.btn-small{display:inline-block;margin-top:13px;width:89px;height:35px;line-height:35px;text-align:center;background:linear-gradient(#1ca4dd,#0180b8);color:var(--white);font-size:11px;text-transform:uppercase;box-shadow:0 3px 2px rgba(0,0,0,.35)}

/* band */
.promo{position:absolute;left:0;top:1308px;width:1200px;height:322px;background:
  radial-gradient(ellipse at 20% 25%,#1d5a66 0%,#0c2a33 30%,#000 60%),var(--black);text-align:center;color:var(--white)}
.promo-title{position:absolute;left:0;top:72px;width:1200px;font-size:31px;font-weight:400}
.promo-rule{position:absolute;left:238px;top:128px;width:725px;height:1px;background:#555}
.promo-text{position:absolute;left:300px;top:142px;width:600px;font-size:12.5px;line-height:22px}
.btn-outline{position:absolute;left:531px;top:208px;width:138px;height:36px;line-height:33px;border:1.5px solid var(--white);font-size:17px;text-transform:uppercase;letter-spacing:.5px}

/* projects */
.project{position:absolute;top:1742px;width:270px}
.project-title{font-size:13.5px;color:var(--brand);font-weight:400}
.project-date{font-size:12.5px;font-weight:700;color:var(--ink);margin-top:4px}
.project-text{font-size:12.5px;line-height:23px;color:var(--body);margin-top:6px}

/* footer */
.site-footer{position:absolute;left:0;top:1925px;width:1200px;height:331px;background:var(--black);color:var(--white)}
.footer-heading{position:absolute;top:20px;font-size:22px;font-weight:400;display:flex;align-items:center;gap:8px}
.feed-item{position:absolute;width:270px}
.feed-title{font-size:13.5px;font-weight:600}
.feed-date{font-size:12px;color:var(--muted);margin-top:3px}
.feed-text{font-size:12px;line-height:22px;color:var(--muted)}
.contact-line{position:absolute;left:916px;font-size:12px;color:var(--muted)}
.footer-rule{position:absolute;left:0;top:280px;width:1200px;height:1px;background:#333}
.copyright{position:absolute;left:0;top:297px;width:1200px;text-align:center;font-size:12px;color:#ddd}
</style>
</head>
<body>

<header class="site-header">
  <div class="brand"><span class="brand-mark"></span><span class="brand-name">BRTL</span></div>
  <div class="brand-sub">Coastal Linkage Engineering Service</div>
  <div class="support">
    <div class="support-label">Phone Support</div>
    <div class="support-number">
      <svg width="18" height="18" viewBox="0 0 24 24"><path fill="#0292cd" d="M6.6 10.8c1.4 2.8 3.8 5.1 6.6 6.6l2.2-2.2c.3-.3.7-.4 1-.2 1.1.4 2.3.6 3.6.6.6 0 1 .4 1 1V20c0 .6-.4 1-1 1C10.6 21 3 13.4 3 4c0-.6.4-1 1-1h3.5c.6 0 1 .4 1 1 0 1.3.2 2.5.6 3.6.1.3 0 .7-.2 1z"/></svg>
      1300 555 214
    </div>
  </div>
</header>

<nav class="main-nav">
  <span class="nav-item" style="left:105px">Home</span>
  <span class="nav-item active" style="left:173px">Services</span>
  <span class="nav-item" style="left:328px">About Us</span>
  <span class="nav-item" style="left:456px">Certifications</span>
  <span class="nav-item" style="left:629px">Current / Past Projects</span>
  <span class="nav-item" style="left:883px">Contact Us</span>
</nav>
<ul class="submenu">
  <li>Fibre Optics</li>
  <li>Security</li>
  <li>Building Services</li>
  <li>Electrical</li>
</ul>

<section class="hero" role="img" aria-label="Close-up photo of a fibre optic fusion splicer with green cables and a blue tray">
  <div class="hero-caption" style="left:53px;top:164px">
    <div class="hero-kicker">Mauris lacus vitae felis</div>
    <div class="hero-title">Fibre Optics &amp; Security</div>
    <p class="hero-text">Mauris vel lacus vitae felis vestibulum volutpat Etiam est nunc venenatis in tristique eu imperdiet ac nisl Cum sociis</p>
    <div class="hero-dots"><span></span><span></span><span></span><span></span></div>
  </div>
</section>

<h2 class="section-title" style="left:54px;top:758px">About BRTL Group</h2>
<p class="about-text">BRTL is diversified technology company 100% Australian owned and operated, we provide Communication, Electrical, Security &amp; ICT services for residential and commercial customers. With over 100 years of combined industry knowledge we pride ourselves on innovated solutions that utilises technology advancements which delivers on our customer's expectations.</p>

<article class="service" style="left:53px">
  <div class="service-photo" role="img" aria-label="Photo of a technician splicing fibre optic cable" style="background:linear-gradient(135deg,#2d3a35,#5b6e5a 50%,#2a2d30)"></div>
  <h3 class="service-title">Fibre Optics</h3>
  <p class="service-text">Proin gravida nibh vel velit auctored aliquetenean sollicitudin lorem quis bibendum auctornisi elit.</p>
  <span class="btn-small">Read More</span>
</article>
<article class="service" style="left:338px">
  <div class="service-photo" role="img" aria-label="Photo of several white security cameras on a pole" style="background:linear-gradient(135deg,#2a2630,#d8d8dc 55%,#4a4550)"></div>
  <h3 class="service-title">Security</h3>
  <p class="service-text">Proin gravida nibh vel velit auctored aliquetenean sollicitudin lorem quis bibendum auctornisi elit.</p>
  <span class="btn-small">Read More</span>
</article>
<article class="service" style="left:624px">
  <div class="service-photo" role="img" aria-label="Photo of a person using a blue touchscreen building control interface" style="background:linear-gradient(135deg,#0a5aa8,#3fb2e6 55%,#0a4d8f)"></div>
  <h3 class="service-title">Building Services</h3>
  <p class="service-text">Proin gravida nibh vel velit auctored aliquetenean sollicitudin lorem quis bibendum auctornisi elit.</p>
  <span class="btn-small">Read More</span>
</article>
<article class="service" style="left:905px">
  <div class="service-photo" role="img" aria-label="Photo of electrical conduits and pipework in a plant room" style="background:linear-gradient(135deg,#8d8a86,#d9d6d0 50%,#6f6a66)"></div>
  <h3 class="service-title">Electrical</h3>
  <p class="service-text">Proin gravida nibh vel velit auctored aliquetenean sollicitudin lorem quis bibendum auctornisi elit.</p>
  <span class="btn-small">Read More</span>
</article>

<section class="promo" role="img" aria-label="Background photo of glowing fibre optic strands on black">
  <h2 class="promo-title">BRTL offers a wide range of IP commercial security solutions</h2>
  <div class="promo-rule"></div>
  <p class="promo-text">Proin gravida nibh vel velit auctor aliquet. Aenean sollicitudin, lorem quis bibendum auctor, nisi elit consequat ipsum, nec sagittis sem nibh id elit.</p>
  <span class="btn-outline">Read More</span>
</section>

<h2 class="section-title" style="left:53px;top:1668px">Current / Past Projects</h2>
<article class="project" style="left:89px">
  <h3 class="project-title">Proin gravida nibh vel velit auctor aliquet</h3>
  <div class="project-date">12 Jan 2015</div>
  <p class="project-text">Lorem Ipsum. Proin gravida nibh vel velit ws uctor aliquet lorem quis bibendum auctor nisi elit consequat ipsum nec sagitti,</p>
</article>
<article class="project" style="left:456px">
  <h3 class="project-title">Gravida nibh vel velit auctor aliquet vild</h3>
  <div class="project-date">12 Jan 2015</div>
  <p class="project-text">Lorem Ipsum. Proin gravida nibh vel velit ws uctor aliquet lorem quis bibendum auctor nisi elit consequat ipsum nec sagitti,</p>
</article>
<article class="project" style="left:836px">
  <h3 class="project-title">Hroin gravida nibh vel velit auctor aliquet</h3>
  <div class="project-date">12 Jan 2015</div>
  <p class="project-text">Lorem Ipsum. Proin gravida nibh vel velit ws uctor aliquet lorem quis bibendum auctor nisi elit consequat ipsum nec sagitti,</p>
</article>

<footer class="site-footer">
  <h2 class="footer-heading" style="left:89px">
    <svg width="14" height="14" viewBox="0 0 14 14"><rect width="14" height="14" rx="2" fill="#f08a24"/><circle cx="3.5" cy="10.5" r="1.5" fill="#fff"/><path d="M2 6a6 6 0 0 1 6 6M2 2.5A9.5 9.5 0 0 1 11.5 12" stroke="#fff" stroke-width="1.6" fill="none"/></svg>
    Rss feed
  </h2>
  <div class="feed-item" style="left:89px;top:57px"><div class="feed-title">Aroin gravida nibh vel velit auctor aliquet</div><div class="feed-date">10 Jan 2015</div><p class="feed-text">Lorem Ipsum. Proin gravida nibh vel velit ws uctor aliquet lorem quis bibendum.</p></div>
  <div class="feed-item" style="left:484px;top:57px"><div class="feed-title">Aroin gravida nibh vel velit auctor aliquet</div><div class="feed-date">10 Jan 2015</div><p class="feed-text">Lorem Ipsum. Proin gravida nibh vel velit ws uctor aliquet lorem quis bibendum.</p></div>
  <div class="feed-item" style="left:89px;top:168px"><div class="feed-title">Aroin gravida nibh vel velit auctor aliquet</div><div class="feed-date">10 Jan 2015</div><p class="feed-text">Lorem Ipsum. Proin gravida nibh vel velit ws uctor aliquet lorem quis bibendum.</p></div>
  <div class="feed-item" style="left:484px;top:168px"><div class="feed-title">Aroin gravida nibh vel velit auctor aliquet</div><div class="feed-date">10 Jan 2015</div><p class="feed-text">Lorem Ipsum. Proin gravida nibh vel velit ws uctor aliquet lorem quis bibendum.</p></div>

  <h2 class="footer-heading" style="left:916px">Contact Details</h2>
  <div class="contact-line" style="top:60px">Suite 4B, 12-14 Harbourline Drive</div>
  <div class="contact-line" style="top:94px">Seabrook NSW 2160</div>
  <div class="contact-line" style="top:129px">PO Box 2280 NSW 1790</div>
  <div class="contact-line" style="top:162px">Telephone 1300 555 214</div>

  <div class="footer-rule"></div>
  <div class="copyright">©Copyright 2014 &nbsp;brtlgroup &nbsp; | &nbsp; All rights reserved &nbsp; | &nbsp; Privacy policy &nbsp; | &nbsp; Terms &amp; Conditions</div>
</footer>

</body>
</html>
```